IV Nutritional Clinic Web Design

We are working with Velqo. They are an IV Nutritional Clinic and in need of a new website design.
Some sites to use for inspiration:
https://brightpathcareco.com
https://www.ourzavrowellness.com
https://www.dewspringlounge.com
https://qvitalsurge.com
https://www.lumo-vital.com/pages/iv-therapy-west-hollywood
https://www.tqoncologyhub.com/cancer-care/iv-drips/
https://dripwellary.com
https://corvinahealthhub.com
Thank you for taking the time to consider designing a website for us. We are web developers based in Stockton, CA, USA. Most of our projects go through the same process. Understanding this process may help you win a project with us. We custom-code all of our websites in-house. We don’t have any requirements as to what tools you use for your design, but we prefer Figma files. For any design that we label as four-stars, we send it to the client for review. The client picks the final design they want us to use. Once we complete this process, we will continue to show additional clients all the four-star sites and purchase them later. Your designs will have multiple chances to sell. For better chances of success, we ask that you follow these guidelines.
IMAGES:
If you use any images or icons in the design, we ask that you have a link to the asset so we can purchase the image/icon. Most of the designs we submit do not have the customer’s images on them unless they have some great images. Be creative; show us the feeling you are trying to portray with your image choices. Use any royalty-free site you choose. We subscribe to Pixvane and mainly use their images, but we can purchase images outside of Pixvane.
PLEASE NOTE: we will not submit designs to clients with watermarks on the images.
FONTS:
We ask that you identify the fonts used in the design. This can be done in a message if you want. We typically use Google Fonts and Pixvane Fonts.
CONTENT:
We're always open to different content and ideas. We often submit designs with stock images so the client can see our vision. We typically take pictures after the website launch to use their images with our vision. Lorem Ipsum is fine for paragraphs, but we ask that you write the headers in correct English. We want to be able to show the vision and identify the sections of the website.
INSPIRATION:
We typically add a couple of links in the brief of websites we like to help you get started in your design.
REVISIONS:
We do not often ask for revisions of the designs unless we see something in the design that may not appeal to the client. If there are slight changes that we want to make, we do that in the development process.
FEEDBACK:
We rarely give feedback on designs during the design process. We are working on many website projects and do not have the time to provide feedback. We usually respond if your request is well thought out and asks specific questions, but a note asking “feedback, please” usually goes unanswered.

```html
<!DOCTYPE html>
<html lang="en">
<head>
<meta charset="utf-8">
<title>Velqo Hydration – IV Nutritional Clinic</title>
<link href="https://fonts.googleapis.com/css2?family=Lexend:wght@300;400;500&display=swap" rel="stylesheet">
<style>
:root{
  --navy:#2a3a8f;
  --green:#84a843;
  --green-soft:#eef2e4;
  --card:#f5f5f6;
  --card-line:#e6e6e8;
  --text:#2b2b2b;
  --muted:#d9dbd6;
  --sky-top:#eef3f8;
  --sky-bottom:#c9dbea;
  --white:#ffffff;
}
*{box-sizing:border-box;margin:0;padding:0}
html,body{width:1200px;height:3934px;overflow:hidden}
body{position:relative;font-family:"Lexend",sans-serif;color:var(--text);background:var(--white)}
.abs{position:absolute}
.navy{color:var(--navy)}
.green{color:var(--green)}
h1,h2{font-weight:500;text-transform:uppercase;letter-spacing:-.5px}
p{font-weight:300}
.btn{position:absolute;display:flex;align-items:center;justify-content:center;background:var(--navy);color:var(--white);border-radius:22px;font-size:13px;text-transform:uppercase;box-shadow:3px 0 0 var(--white),4px 1px 0 var(--navy);text-decoration:none}
.drop{display:inline-block;width:20px;height:22px;vertical-align:middle;margin-left:12px}

/* hero */
.hero-bg{left:0;top:0;width:1200px;height:600px;background:linear-gradient(180deg,var(--sky-top),var(--sky-bottom))}
.logo-badge{left:183px;top:-20px;width:135px;height:134px;border-radius:50%;background:var(--white);display:flex;align-items:center;justify-content:center;padding-top:14px}
.logo-badge span{font-size:30px;font-weight:500;color:var(--navy);letter-spacing:1px}
.nav{left:312px;top:34px;width:708px;height:40px;background:var(--white);border-radius:20px;display:flex;align-items:center;gap:0;padding-left:48px;font-size:12px;text-transform:uppercase;color:#555}
.nav a{color:#555;text-decoration:none;margin-right:42px}
.nav a.active{color:var(--navy)}
.hero h1{font-size:28px;line-height:50px}
.hero-copy{left:111px;top:178px;width:480px}
.hero-copy p{font-size:15px;line-height:35px;margin-top:18px}
.hero-art{left:745px;top:84px;width:280px;height:482px;border-radius:40px 40px 20px 20px;background:linear-gradient(160deg,#dfe8ef,#9fb6c8 60%,#7f8fa0)}

/* about */
.about-photo{left:111px;top:638px;width:449px;height:568px;border-radius:0 70px 0 70px;background:linear-gradient(150deg,#e9e7e3,#c9b58a 40%,#9aa9b6 75%,#d9d6cf)}
.about-frame{left:103px;top:646px;width:449px;height:562px;border:2px solid var(--navy);border-right:none;border-top:none;border-radius:0 0 0 70px}
.about-frame:after{content:"";position:absolute;left:0;top:0;height:100%;border-left:2px solid var(--navy)}
.about-copy{left:637px;top:648px;width:440px;color:var(--white)}
.about-copy h2{font-size:30px;color:var(--navy)}
.about-copy h2 em{font-style:normal;color:var(--white)}
.about-copy p{font-size:14.5px;line-height:34.5px;margin-top:32px}
.about-copy p + p{margin-top:16px}

/* services */
.services-head{left:110px;top:1280px}
.services-head h2{font-size:31px;line-height:50px}
.services-intro{left:609px;top:1281px;width:490px;font-size:14.5px;line-height:34.5px}
.card{position:absolute;width:316px;height:258px;background:var(--card);border:1px solid var(--card-line);border-radius:4px;text-align:center;padding-top:22px}
.card svg{width:60px;height:62px}
.card h3{font-weight:400;font-size:15px;color:var(--navy);text-transform:uppercase;margin-top:14px}
.card p{font-size:13.5px;line-height:33px;margin:6px 22px 0}
.card.more{background:linear-gradient(135deg,#a9c36e,#86a64a 55%,#6f8f3c);border:none;display:flex;align-items:center;justify-content:center;padding:0}
.card.more a{color:var(--white);font-size:15px;text-transform:uppercase;text-decoration:underline}

/* how it works */
.how-bg{left:0;top:2040px;width:1200px;height:836px}
.how-head{left:0;top:2160px;width:1200px;text-align:center}
.how-head h2{font-size:31px}
.how-head p{font-size:14.5px;line-height:34.5px;margin:18px auto 0;width:880px}
.big-num{position:absolute;font-size:76px;font-weight:500;color:var(--muted);line-height:1;opacity:.8}
.step{position:absolute;width:280px;height:280px}
.step .shape{position:absolute;left:41px;top:41px;width:198px;height:198px;transform:rotate(45deg);border:3px solid var(--green);border-radius:36px;background:var(--green-soft)}
.step.navy-step .shape{border-color:var(--navy)}
.step .inner{position:absolute;left:0;top:56px;width:280px;text-align:center}
.step svg.icon{width:50px;height:50px}
.step h4{font-weight:400;font-size:15px;line-height:33px;text-transform:uppercase;margin-top:8px}
.step .go{display:inline-block;width:28px;height:28px;margin-top:14px}

/* testimonials */
.testi-head{left:113px;top:2950px;width:340px}
.testi-head h2{font-size:31px;line-height:50px}
.testi-head p{font-size:14px;line-height:34px;margin-top:22px}
.arrow-btn{position:absolute;top:3189px;width:26px;height:26px;border-radius:50%}
.tcard{position:absolute;top:2959px;width:280px;height:224px;background:var(--card);border-radius:4px;padding:18px 22px}
.stars{color:#f0c040;font-size:17px;letter-spacing:4px}
.tcard p{font-style:italic;font-size:14px;line-height:31.5px;margin-top:8px}
.person{position:absolute;top:3205px;display:flex;align-items:center;gap:20px}
.avatar{width:56px;height:56px;border-radius:50%;background:linear-gradient(160deg,#c9b7a2,#7b8a9c)}
.person b{display:block;font-weight:400;font-size:13px;color:var(--green);text-transform:uppercase}
.person span{display:block;font-size:13.5px;text-transform:uppercase;margin-top:6px}

/* cta */
.cta{left:0;top:3348px;width:1200px;height:226px;background:var(--green)}
.cta h2{position:absolute;left:113px;top:52px;font-size:31px;color:var(--white)}
.cta h2 em{font-style:normal;color:var(--navy)}
.cta p{position:absolute;left:113px;top:112px;width:560px;color:var(--white);font-size:14.5px;line-height:34.5px}

/* footer */
.footer{left:0;top:3574px;width:1200px;height:360px;background:var(--navy);color:var(--white)}
.f-logo{position:absolute;left:107px;top:64px;font-size:56px;font-weight:500;letter-spacing:4px}
.f-social{position:absolute;left:150px;top:186px;display:flex;gap:8px}
.f-social i{width:26px;height:26px;border:2px solid var(--white);border-radius:50%;display:block}
.f-copy{position:absolute;left:98px;top:248px;font-size:14px;font-weight:300}
.f-col{position:absolute;top:64px}
.f-col h5{font-weight:400;font-size:17px;color:var(--green);text-transform:uppercase}
.f-col ul{list-style:none;margin-top:20px}
.f-col li{font-size:14px;font-weight:300;line-height:34px}
.contact li{display:flex;align-items:flex-start;gap:18px;line-height:26px;margin-bottom:24px}
.contact i{flex:none;width:32px;height:32px;border-radius:50%;background:var(--green);display:flex;align-items:center;justify-content:center}
</style>
</head>
<body>

<!-- HERO -->
<div class="abs hero-bg"></div>
<svg class="abs" style="left:0;top:500px" width="1200" height="700" viewBox="0 0 1200 700" aria-hidden="true">
  <path d="M0 14 C200 70 420 90 620 70 C860 46 1040 10 1200 0 L1200 520 C1040 610 860 690 610 690 C380 690 160 600 0 622 Z" fill="#84a843"/>
</svg>
<div class="abs hero-art" role="img" aria-label="IV drip bag filled with water and fresh fruit slices"></div>

<div class="abs logo-badge"><span>VELQO</span></div>
<nav class="abs nav">
  <a class="active" href="#">Home</a><a href="#">About</a><a href="#">Services</a><a href="#">IV Therapies</a><a href="#">Testimonials</a><a href="#">Contact</a>
  <svg width="12" height="12" viewBox="0 0 12 12"><circle cx="5" cy="5" r="3.5" fill="none" stroke="#555" stroke-width="1.3"/><path d="M7.6 7.6 10.5 10.5" stroke="#555" stroke-width="1.3"/></svg>
</nav>

<section class="abs hero-copy hero">
  <h1 class="navy">Nourishment for your body,</h1>
  <h1 class="green">Clarity for your mind</h1>
  <p>Lorem ipsum dolor sit amet, consectetur adipiscing elit, sed do eiusmod tempor incididunt ut labore et dolore magna aliqua enim ad minim veniam.</p>
</section>
<a class="btn" href="#" style="left:111px;top:409px;width:208px;height:38px">Book an appointment</a>

<!-- ABOUT -->
<div class="abs about-frame"></div>
<div class="abs about-photo" role="img" aria-label="Woman relaxing in a clinic chair reading a wellness menu"></div>
<section class="abs about-copy">
  <h2>About <em>Velqo Hydration</em>
    <svg class="drop" viewBox="0 0 20 22"><rect x="3" y="3" width="10" height="13" rx="2" fill="none" stroke="#fff" stroke-width="1.8"/><path d="M8 16v5M15 6c2 3 3 4 3 6a3 3 0 0 1-6 0c0-2 1-3 3-6z" fill="none" stroke="#fff" stroke-width="1.6"/></svg></h2>
  <p>Lorem ipsum dolor sit amet, consectetur adipiscing elit, sed do eiusmod tempor incididunt ut labore et dolore magna aliqua. Ut enim ad minim veniam, quis nostrud exercitation ullamco laboris nisi ut aliquip ex ea commodo consequat. Duis aute irure dolor in reprehenderit in voluptate velit esse cillum dolore eu fugiat nulla pariatur.</p>
  <p>Lorem ipsum dolor sit amet, consectetur adipiscing elit, sed do eiusmod tempor incididunt ut labore et dolore magna aliqua enim ad minim veniam.</p>
</section>
<a class="btn" href="#" style="left:637px;top:1069px;width:134px;height:36px">Learn more</a>

<!-- SERVICES -->
<section class="abs services-head">
  <h2 class="navy">Velqo Hydration</h2>
  <h2 class="green">Services
    <svg class="drop" viewBox="0 0 20 22"><rect x="3" y="3" width="10" height="13" rx="2" fill="none" stroke="#84a843" stroke-width="1.8"/><path d="M8 16v5M15 6c2 3 3 4 3 6a3 3 0 0 1-6 0c0-2 1-3 3-6z" fill="none" stroke="#84a843" stroke-width="1.6"/></svg></h2>
</section>
<p class="abs services-intro">Lorem ipsum dolor sit amet, consectetur adipiscing elit, sed do eiusmod tempor incididunt ut labore et dolore magna aliqua enim ad minim veniam quis nostrud exercitation.</p>

<div class="card" style="left:110px;top:1441px">
  <svg viewBox="0 0 60 62"><rect x="12" y="18" width="16" height="38" rx="3" fill="none" stroke="#2a3a8f" stroke-width="2"/><rect x="15" y="10" width="10" height="8" fill="none" stroke="#2a3a8f" stroke-width="2"/><rect x="30" y="34" width="16" height="22" fill="none" stroke="#2a3a8f" stroke-width="2"/><path d="M40 6c4 5 6 8 6 11a6 6 0 0 1-12 0c0-3 2-6 6-11z" fill="none" stroke="#84a843" stroke-width="2"/></svg>
  <h3>IV Hydration Therapy</h3>
  <p>Lorem ipsum dolor sit amet, consectetur adipiscing elit, sed do eiusmod tempor incididunt ut labore et</p>
</div>
<div class="card" style="left:443px;top:1441px">
  <svg viewBox="0 0 60 62"><path d="M28 6 46 13v16c0 14-9 22-18 26C19 51 10 43 10 29V13z" fill="none" stroke="#2a3a8f" stroke-width="2"/><path d="M24 22h8v8h8v8h-8v8h-8v-8h-8v-8h8z" fill="none" stroke="#2a3a8f" stroke-width="2"/><circle cx="46" cy="46" r="6" fill="none" stroke="#84a843" stroke-width="2"/></svg>
  <h3>Immune Boost IV</h3>
  <p>Lorem ipsum dolor sit amet, consectetur adipiscing elit, sed do eiusmod tempor incididunt ut labore et</p>
</div>
<div class="card" style="left:774px;top:1441px">
  <svg viewBox="0 0 60 62"><rect x="14" y="6" width="18" height="8" fill="none" stroke="#2a3a8f" stroke-width="2"/><rect x="10" y="14" width="26" height="42" rx="4" fill="none" stroke="#2a3a8f" stroke-width="2"/><rect x="14" y="28" width="18" height="12" fill="none" stroke="#84a843" stroke-width="2"/><rect x="40" y="30" width="10" height="22" rx="5" fill="none" stroke="#2a3a8f" stroke-width="2"/></svg>
  <h3>Vitamin B12 Shots</h3>
  <p>Lorem ipsum dolor sit amet, consectetur adipiscing elit, sed do eiusmod tempor incididunt ut labore et</p>
</div>
<div class="card" style="left:110px;top:1719px">
  <svg viewBox="0 0 60 62"><rect x="10" y="10" width="28" height="34" rx="4" fill="none" stroke="#2a3a8f" stroke-width="2"/><path d="M16 18h16M16 24h16M24 44v12" stroke="#2a3a8f" stroke-width="2"/><path d="M44 26c4 6 7 9 7 13a7 7 0 0 1-14 0c0-4 3-7 7-13z" fill="none" stroke="#84a843" stroke-width="2"/></svg>
  <h3>Hangover Recovery IV</h3>
  <p>Lorem ipsum dolor sit amet, consectetur adipiscing elit, sed do eiusmod tempor incididunt ut labore et</p>
</div>
<div class="card" style="left:443px;top:1719px">
  <svg viewBox="0 0 60 62"><rect x="20" y="4" width="20" height="8" fill="none" stroke="#2a3a8f" stroke-width="2"/><rect x="16" y="12" width="28" height="46" rx="5" fill="none" stroke="#2a3a8f" stroke-width="2"/><path d="M30 44c-6-4-7-10-4-14 3 3 4 8 4 14zm0 0c6-4 7-10 4-14-3 3-4 8-4 14z" fill="none" stroke="#84a843" stroke-width="2"/></svg>
  <h3>Detox &amp; Cleanse IV</h3>
  <p>Lorem ipsum dolor sit amet, consectetur adipiscing elit, sed do eiusmod tempor incididunt ut labore et</p>
</div>
<div class="card more" style="left:774px;top:1719px" role="img" aria-label="Clinician reviewing a patient chart, tinted green">
  <a href="#">View more services</a>
  <svg width="26" height="12" viewBox="0 0 26 12" style="margin-left:12px"><path d="M1 6h22M18 1l5 5-5 5" fill="none" stroke="#fff" stroke-width="1.8"/></svg>
</div>

<!-- HOW IT WORKS -->
<svg class="abs how-bg" viewBox="0 0 1200 836" aria-hidden="true">
  <path d="M0 14 C300 -4 900 -4 1200 14 L1200 836 L0 836 Z" fill="#eef2e4"/>
</svg>
<section class="abs how-head">
  <h2><span class="navy">How it</span> <span class="green">works</span>
    <svg class="drop" viewBox="0 0 20 22"><rect x="3" y="3" width="10" height="13" rx="2" fill="none" stroke="#84a843" stroke-width="1.8"/><path d="M8 16v5M15 6c2 3 3 4 3 6a3 3 0 0 1-6 0c0-2 1-3 3-6z" fill="none" stroke="#84a843" stroke-width="1.6"/></svg></h2>
  <p>Lorem ipsum dolor sit amet, consectetur adipiscing elit, sed do eiusmod tempor incididunt ut labore et dolore magna aliqua enim ad minim veniam, quis nostrud exercitation ullamco laboris nisi.</p>
</section>

<span class="big-num" style="left:96px;top:2360px">01</span>
<span class="big-num" style="left:424px;top:2360px">03</span>
<span class="big-num" style="left:772px;top:2360px">05</span>
<span class="big-num" style="left:266px;top:2745px">02</span>
<span class="big-num" style="left:830px;top:2745px">04</span>

<div class="step" style="left:115px;top:2360px">
  <div class="shape"></div>
  <div class="inner">
    <svg class="icon" viewBox="0 0 50 50"><rect x="6" y="10" width="38" height="32" rx="3" fill="none" stroke="#2a3a8f" stroke-width="2"/><path d="M6 18h38M15 6v8M35 6v8" stroke="#2a3a8f" stroke-width="2"/><path d="M29 33l4 4 7-8" fill="none" stroke="#84a843" stroke-width="2"/></svg>
    <h4>Schedule<br>your appointment</h4>
    <svg class="go" viewBox="0 0 28 28"><circle cx="14" cy="14" r="12" fill="none" stroke="#84a843" stroke-width="1.6"/><path d="M9 14h10M15 10l4 4-4 4" fill="none" stroke="#84a843" stroke-width="1.6"/></svg>
  </div>
</div>
<div class="step navy-step" style="left:286px;top:2532px">
  <div class="shape"></div>
  <div class="inner">
    <svg class="icon" viewBox="0 0 50 50"><circle cx="14" cy="20" r="5" fill="none" stroke="#2a3a8f" stroke-width="2"/><circle cx="36" cy="20" r="5" fill="none" stroke="#2a3a8f" stroke-width="2"/><path d="M6 42c0-8 4-14 8-14s8 6 8 14M28 42c0-8 4-14 8-14s8 6 8 14" fill="none" stroke="#2a3a8f" stroke-width="2"/><rect x="18" y="4" width="14" height="9" rx="2" fill="none" stroke="#84a843" stroke-width="2"/></svg>
    <h4>Personalized<br>consultation</h4>
    <svg class="go" viewBox="0 0 28 28"><circle cx="14" cy="14" r="12" fill="none" stroke="#2a3a8f" stroke-width="1.6"/><path d="M9 14h10M15 10l4 4-4 4" fill="none" stroke="#2a3a8f" stroke-width="1.6"/></svg>
  </div>
</div>
<div class="step" style="left:458px;top:2360px">
  <div class="shape"></div>
  <div class="inner">
    <svg class="icon" viewBox="0 0 50 50"><rect x="8" y="6" width="18" height="24" rx="3" fill="none" stroke="#2a3a8f" stroke-width="2"/><path d="M17 30v12M30 44V22a3 3 0 0 1 6 0v10h4a4 4 0 0 1 4 4v8" fill="none" stroke="#84a843" stroke-width="2"/></svg>
    <h4>Your IV therapy<br>session</h4>
    <svg class="go" viewBox="0 0 28 28"><circle cx="14" cy="14" r="12" fill="none" stroke="#84a843" stroke-width="1.6"/><path d="M9 14h10M15 10l4 4-4 4" fill="none" stroke="#84a843" stroke-width="1.6"/></svg>
  </div>
</div>
<div class="step navy-step" style="left:630px;top:2532px">
  <div class="shape"></div>
  <div class="inner">
    <svg class="icon" viewBox="0 0 50 50"><circle cx="22" cy="16" r="8" fill="none" stroke="#2a3a8f" stroke-width="2"/><path d="M4 40l10-6h14a3 3 0 0 1 0 6H20M28 36l12-6a3 3 0 0 1 3 5L30 44H10" fill="none" stroke="#2a3a8f" stroke-width="2"/><path d="M18 16l3 3 5-6" fill="none" stroke="#84a843" stroke-width="2"/></svg>
    <h4>Feel the<br>benefits</h4>
    <svg class="go" viewBox="0 0 28 28"><circle cx="14" cy="14" r="12" fill="none" stroke="#2a3a8f" stroke-width="1.6"/><path d="M9 14h10M15 10l4 4-4 4" fill="none" stroke="#2a3a8f" stroke-width="1.6"/></svg>
  </div>
</div>
<div class="step" style="left:804px;top:2360px">
  <div class="shape"></div>
  <div class="inner">
    <svg class="icon" viewBox="0 0 50 50"><circle cx="22" cy="16" r="8" fill="none" stroke="#2a3a8f" stroke-width="2"/><path d="M8 44c0-10 6-16 14-16s14 6 14 16" fill="none" stroke="#2a3a8f" stroke-width="2"/><circle cx="40" cy="12" r="5" fill="none" stroke="#84a843" stroke-width="2"/></svg>
    <h4>Follow-up &amp;<br>maintenance</h4>
    <svg class="go" viewBox="0 0 28 28"><circle cx="14" cy="14" r="12" fill="none" stroke="#84a843" stroke-width="1.6"/><path d="M9 14h10M15 10l4 4-4 4" fill="none" stroke="#84a843" stroke-width="1.6"/></svg>
  </div>
</div>
<svg class="abs" style="left:0;top:2540px" width="1200" height="100" viewBox="0 0 1200 100" aria-hidden="true">
  <g fill="none" stroke-width="2.2">
    <path d="M340 56l24 24M352 80h12V68" stroke="#84a843"/>
    <path d="M508 80l24-24M520 56h12v12" stroke="#2a3a8f"/>
    <path d="M684 56l24 24M696 80h12V68" stroke="#84a843"/>
    <path d="M852 80l24-24M864 56h12v12" stroke="#2a3a8f"/>
  </g>
</svg>

<!-- TESTIMONIALS -->
<section class="abs testi-head">
  <h2 class="navy">What our</h2>
  <h2 class="green">Customers says
    <svg class="drop" viewBox="0 0 20 22"><rect x="3" y="3" width="10" height="13" rx="2" fill="none" stroke="#84a843" stroke-width="1.8"/><path d="M8 16v5M15 6c2 3 3 4 3 6a3 3 0 0 1-6 0c0-2 1-3 3-6z" fill="none" stroke="#84a843" stroke-width="1.6"/></svg></h2>
  <p>Lorem ipsum dolor sit amet, consectetur elit sed do eiusmod tempor incididunt ut labore et dolore magna aliqua</p>
</section>
<svg class="arrow-btn" style="left:113px" viewBox="0 0 26 26"><circle cx="13" cy="13" r="13" fill="#111"/><path d="M15 8l-5 5 5 5" fill="none" stroke="#fff" stroke-width="2"/></svg>
<svg class="arrow-btn" style="left:162px" viewBox="0 0 26 26"><circle cx="13" cy="13" r="13" fill="#84a843"/><path d="M11 8l5 5-5 5" fill="none" stroke="#fff" stroke-width="2"/></svg>

<div class="tcard" style="left:504px"><div class="stars">★★★★★</div><p>"Lorem ipsum dolor sit amet, consectetur adipiscing elit, sed do eiusmod tempor incididunt ut labore et dolore magna aliqua. Ut enim ad minim veniam...</p></div>
<div class="tcard" style="left:805px"><div class="stars">★★★★★</div><p>"Lorem ipsum dolor sit amet, consectetur adipiscing elit, sed do eiusmod tempor incididunt ut labore et dolore magna aliqua. Ut enim ad minim veniam...</p></div>
<div class="tcard" style="left:1102px"><div class="stars">★★★★★</div><p>"Lorem ipsum dolor sit amet, consectetur adipiscing elit, sed do eiusmod tempor incididunt ut labore et dolore magna aliqua. Ut enim ad minim veniam...</p></div>

<div class="person" style="left:520px"><div class="avatar" role="img" aria-label="Customer portrait"></div><div><b>Nora P</b><span>San Diego, CA</span></div></div>
<div class="person" style="left:820px"><div class="avatar" role="img" aria-label="Customer portrait"></div><div><b>Evan T</b><span>Los Angeles, CA</span></div></div>
<div class="person" style="left:1120px"><div class="avatar" role="img" aria-label="Customer portrait"></div></div>

<!-- CTA -->
<section class="abs cta">
  <h2><em>Schedule a</em> consultation
    <svg class="drop" viewBox="0 0 20 22"><rect x="3" y="3" width="10" height="13" rx="2" fill="none" stroke="#fff" stroke-width="1.8"/><path d="M8 16v5M15 6c2 3 3 4 3 6a3 3 0 0 1-6 0c0-2 1-3 3-6z" fill="none" stroke="#fff" stroke-width="1.6"/></svg></h2>
  <p>Lorem ipsum dolor sit amet, consectetur adipiscing elit, sed do eiusmod tempor incididunt ut labore et dolore magna.</p>
  <a class="btn" href="#" style="left:855px;top:92px;width:226px;height:42px;font-size:14px">Book an appointment</a>
</section>

<!-- FOOTER -->
<footer class="abs footer">
  <div class="f-logo">VELQO</div>
  <div class="f-social"><i></i><i></i><i></i><i></i></div>
  <div class="f-copy">Copyright © 2025 Velqo Hydration</div>

  <div class="f-col" style="left:470px"><h5>Quick links</h5>
    <ul><li>Home</li><li>About</li><li>Services</li><li>IV Therapies</li><li>Testimonials</li><li>Contact</li></ul></div>
  <div class="f-col" style="left:701px"><h5>Other links</h5>
    <ul><li>Privacy Policy</li><li>Terms of Use</li><li>Site Map</li><li>Cookies</li><li>Information</li></ul></div>
  <div class="f-col contact" style="left:933px"><h5>Contact us</h5>
    <ul>
      <li><i><svg width="14" height="14" viewBox="0 0 14 14"><path d="M3 1l2 3-1.5 1.5a8 8 0 0 0 5 5L10 9l3 2-1 2C6 13 1 8 1 2z" fill="#fff"/></svg></i><span>+1 888 888 8888</span></li>
      <li><i><svg width="14" height="12" viewBox="0 0 14 12"><rect x="1" y="1" width="12" height="10" rx="1" fill="none" stroke="#fff" stroke-width="1.5"/><path d="M1 2l6 5 6-5" fill="none" stroke="#fff" stroke-width="1.5"/></svg></i><span>hello@velqomail.com</span></li>
      <li><i><svg width="12" height="16" viewBox="0 0 12 16"><path d="M6 15S1 9 1 6a5 5 0 0 1 10 0c0 3-5 9-5 9z" fill="#fff"/><circle cx="6" cy="6" r="2" fill="#84a843"/></svg></i><span>23, Velqo Lorem<br>908 738</span></li>
    </ul></div>
</footer>

</body>
</html>
```